Classic Car Web Banner Set Design

We need a set of banner ads designed for a manufacturing and retail company that sells weatherstripping for classic American vehicles (muscle cars, antique cars, classic cars). The banner ad must include our logo. There should be at least one car in the graphic, whole or partial. Our primary colors are Red and Black. Either a representation of auto weatherstripping or the words "Quality Weatherstripping" should be in the design.

Company name is "Marwick Gasket Products"

Sizes Needed: 300x250, 300x100, 728x90, 160x600, 120x90, 728x90, 234x60, 320x100, 750x100, 250x250

Target Market(s)

Consumer Audience, Classic Car Market

Industry/Entity Type

Retail

Font styles to use
Sans Serif

Colors
ec1f27

Requirements
Must have
• Red and Black primary colors. Company logo. Graphically show weatherstripping and/or automotive icons. If a vehicle is used, it must be an American vehicle.
Nice to have
• PSD files for selected entry.
Should not have
• no people

```html
<!DOCTYPE html>
<html lang="en">
<head>
<meta charset="utf-8">
<title>Marwick Gasket Products – Banner Set</title>
<link href="https://fonts.googleapis.com/css2?family=Arimo:wght@700&display=swap" rel="stylesheet">
<style>
  :root {
    --page: #ffffff;
    --black: #000000;
    --red: #ec1f27;
    --red-light: #ff4a4f;
    --red-dark: #b5121a;
    --icon-dark: #4a070a;
    --gold: #f8a51c;
    --gold-light: #ffc24a;
    --panel-light: #ffffff;
    --panel-grey: #cfcfcf;
    --photo-light: #8a8a8a;
    --photo-mid: #4d4d4d;
    --photo-dark: #262626;
    --rubber: #141414;
    --car-maroon: #6b2236;
    --car-plum: #8c4a6a;
    --car-grey: #9a9a9a;
    --silver: #d9d9d9;
    --silver-dark: #8e8e8e;
    --label: #222222;
  }
  * { box-sizing: border-box; margin: 0; padding: 0; }
  html, body { width: 1200px; height: 1200px; overflow: hidden; background: var(--page); }
  body { font-family: "Arimo", Arial, sans-serif; }

  .sheet {
    position: absolute; left: 0; top: 0;
    width: 850px; height: 850px;
    transform: scale(1.41176); transform-origin: 0 0;
  }
  .banner { position: absolute; overflow: hidden; background: var(--black); border: 1px solid #9a9a9a; }
  .size-label { position: absolute; font-size: 15px; color: var(--label); text-align: center; width: 120px; font-weight: 400; font-family: "Arimo", Arial, sans-serif; }

  .logo-panel {
    position: absolute; display: flex; align-items: center; justify-content: center;
    background: linear-gradient(180deg, var(--panel-light) 0%, var(--panel-light) 45%, var(--panel-grey) 100%);
  }
  .brand-name { color: var(--black); font-weight: 700; text-align: center; line-height: 1.1; }

  .photo { position: absolute; }
  .silver { position: absolute; background: linear-gradient(135deg, #ffffff 0%, var(--silver) 40%, var(--silver-dark) 100%); }

  .headline { position: absolute; text-align: center; color: var(--gold); font-weight: 700; line-height: 1.08; text-shadow: 0 1px 0 #7a4a00; white-space: nowrap; }
  .headline .lead { display: block; color: var(--gold-light); }

  .shop-btn {
    position: absolute; width: 140px; height: 37px; display: flex;
    background: linear-gradient(180deg, var(--red-light) 0%, var(--red) 50%, var(--red-dark) 100%);
    border-radius: 2px; box-shadow: 0 2px 3px rgba(0,0,0,.5);
  }
  .shop-btn .text { flex: 1; display: flex; align-items: center; justify-content: center; color: #fff; font-size: 14px; font-weight: 700; text-shadow: 0 1px 1px rgba(0,0,0,.4); }
  .shop-btn .icon { width: 38px; display: flex; align-items: center; justify-content: center; border-left: 1px solid rgba(255,255,255,.35); }

  /* 728x90 */
  .leaderboard { left: 75px; top: 55px; width: 727px; height: 90px; }
  .leaderboard .logo-panel { left: 0; top: 0; width: 140px; height: 90px; }
  .leaderboard .brand-name { font-size: 14px; width: 120px; }
  .leaderboard .silver { left: 340px; top: 0; width: 400px; height: 90px; clip-path: polygon(0 0, 10% 50%, 0 100%, 100% 100%, 100% 0); }
  .leaderboard .photo {
    left: 352px; top: 0; width: 376px; height: 90px;
    clip-path: polygon(0 0, 10.5% 50%, 0 100%, 100% 100%, 100% 0);
    background:
      radial-gradient(ellipse 26% 30% at 27% 30%, var(--rubber) 0%, var(--rubber) 55%, transparent 100%),
      radial-gradient(ellipse 22% 40% at 44% 72%, var(--car-plum) 0%, var(--car-maroon) 50%, transparent 100%),
      radial-gradient(ellipse 16% 30% at 62% 62%, var(--car-grey) 0%, transparent 100%),
      radial-gradient(ellipse at 50% 40%, var(--photo-light) 0%, var(--photo-mid) 50%, var(--photo-dark) 100%);
  }
  .leaderboard .headline { left: 150px; top: 8px; width: 190px; font-size: 20px; }
  .leaderboard .headline .lead { font-size: 26px; }
  .leaderboard .shop-btn { left: 573px; top: 25px; }

  /* 300x250 */
  .rectangle { left: 69px; top: 292px; width: 300px; height: 250px; }
  .rectangle .logo-panel { left: 0; top: 0; width: 160px; height: 62px; }
  .rectangle .brand-name { font-size: 12px; width: 140px; }
  .rectangle .silver { left: 150px; top: 0; width: 150px; height: 250px; clip-path: polygon(0 0, 100% 0, 100% 100%, 3% 100%, 33% 40%); }
  .rectangle .photo {
    left: 160px; top: 0; width: 140px; height: 250px;
    clip-path: polygon(0 0, 100% 0, 100% 100%, 4% 100%, 33% 40%);
    background:
      radial-gradient(ellipse 50% 16% at 55% 14%, var(--rubber) 0%, var(--rubber) 60%, transparent 100%),
      radial-gradient(ellipse 45% 14% at 70% 52%, var(--car-grey) 0%, #555 60%, transparent 100%),
      radial-gradient(ellipse 55% 20% at 50% 82%, var(--car-plum) 0%, var(--car-maroon) 55%, transparent 100%),
      radial-gradient(ellipse at 50% 40%, var(--photo-light) 0%, var(--photo-mid) 50%, var(--photo-dark) 100%);
  }
  .rectangle .headline { left: 0; top: 88px; width: 168px; font-size: 22px; }
  .rectangle .headline .lead { font-size: 28px; }
  .rectangle .shop-btn { left: 8px; top: 200px; }

  /* 160x600 */
  .skyscraper { left: 635px; top: 210px; width: 160px; height: 600px; }
  .skyscraper .logo-panel { left: 0; top: 0; width: 160px; height: 82px; }
  .skyscraper .brand-name { font-size: 14px; width: 140px; }
  .skyscraper .photo {
    left: 0; top: 82px; width: 160px; height: 330px;
    background:
      radial-gradient(ellipse 55% 18% at 48% 18%, var(--rubber) 0%, var(--rubber) 60%, transparent 100%),
      radial-gradient(ellipse 50% 10% at 60% 52%, var(--car-grey) 0%, #555 60%, transparent 100%),
      radial-gradient(ellipse 60% 14% at 45% 72%, var(--car-plum) 0%, var(--car-maroon) 55%, transparent 100%),
      radial-gradient(ellipse at 50% 40%, var(--photo-light) 0%, var(--photo-mid) 50%, var(--photo-dark) 100%);
  }
  .skyscraper .silver { left: 0; top: 345px; width: 160px; height: 70px; clip-path: polygon(0 60%, 50% 0, 100% 60%, 100% 100%, 0 100%); }
  .skyscraper .black-cut { position: absolute; left: 0; top: 355px; width: 160px; height: 245px; background: var(--black); clip-path: polygon(0 20%, 50% 0, 100% 20%, 100% 100%, 0 100%); }
  .skyscraper .headline { left: 0; top: 428px; width: 160px; font-size: 22px; }
  .skyscraper .headline .lead { font-size: 27px; }
  .skyscraper .shop-btn { left: 11px; top: 543px; }
</style>
</head>
<body>
<main class="sheet">

  <section class="banner leaderboard" aria-label="728 by 90 banner">
    <div class="logo-panel"><span class="brand-name">Marwick Gasket Products</span></div>
    <div class="silver"></div>
    <div class="photo" role="img" aria-label="Black rubber weatherstrip profile and classic American muscle cars"></div>
    <h2 class="headline"><span class="lead">QUALITY</span>WEATHER<br>STRIPPING</h2>
    <a class="shop-btn"><span class="text">SHOP NOW!</span><span class="icon"><svg width="26" height="26" viewBox="0 0 26 26"><circle cx="13" cy="13" r="12" fill="var(--icon-dark)" stroke="#fff" stroke-width="1"/><path d="M10 7.5 L18 13 L10 18.5 Z" fill="#fff"/></svg></span></a>
  </section>
  <div class="size-label" style="left:355px;top:152px;">728X90</div>

  <section class="banner rectangle" aria-label="300 by 250 banner">
    <div class="logo-panel"><span class="brand-name">Marwick Gasket Products</span></div>
    <div class="silver"></div>
    <div class="photo" role="img" aria-label="Black rubber weatherstrip profile above two classic American muscle cars"></div>
    <h2 class="headline"><span class="lead">QUALITY</span>WEATHER<br>STRIPPING</h2>
    <a class="shop-btn"><span class="text">SHOP NOW!</span><span class="icon"><svg width="26" height="26" viewBox="0 0 26 26"><circle cx="13" cy="13" r="12" fill="var(--icon-dark)" stroke="#fff" stroke-width="1"/><path d="M10 7.5 L18 13 L10 18.5 Z" fill="#fff"/></svg></span></a>
  </section>
  <div class="size-label" style="left:154px;top:553px;">300X250</div>

  <section class="banner skyscraper" aria-label="160 by 600 banner">
    <div class="logo-panel"><span class="brand-name">Marwick Gasket Products</span></div>
    <div class="photo" role="img" aria-label="Black rubber weatherstrip profile above two classic American muscle cars"></div>
    <div class="silver"></div>
    <div class="black-cut"></div>
    <h2 class="headline"><span class="lead">QUALITY</span>WEATHER<br>STRIPPING</h2>
    <a class="shop-btn"><span class="text">SHOP NOW!</span><span class="icon"><svg width="26" height="26" viewBox="0 0 26 26"><circle cx="13" cy="13" r="12" fill="var(--icon-dark)" stroke="#fff" stroke-width="1"/><path d="M10 7.5 L18 13 L10 18.5 Z" fill="#fff"/></svg></span></a>
  </section>
  <div class="size-label" style="left:655px;top:818px;">160X600</div>

</main>
</body>
</html>
```